Home Remodeling company needs a business card design

we need a business card design for home remodeling company in hamilton county, indiana USA. we offers a wide range of construction services including whole house renovations, Design and Build Basements and Kitchen and Bathroom Remodeling . we would like to see designs for both site of business card that use the same color of the company logo and also including all information below :
1- Karim Feltous CEO / General Contractor
2- all company contacts Telephone numbers ( 1-888-DULOM-47 ) ( 317-555-0193) email address ( info@dulomhome.com) website ( www.dulomhome.com ) and social media logos (Facebook- twitter- google plus )
3- company logo
4- licensed . insured . bonded

```html
<!DOCTYPE html>
<html lang="en">
<head>
<meta charset="utf-8">
<title>Dulom Home Remodeling – Business Card</title>
<link href="https://fonts.googleapis.com/css2?family=Roboto:wght@400;700&display=swap" rel="stylesheet">
<style>
  :root {
    --backdrop: #3a302b;
    --card: #131314;
    --card-edge: #1d1d1f;
    --gloss: #2c2c2e;
    --white: #f2f2f2;
    --red: #e0261f;
    --muted: #d8d8d8;
  }
  * { box-sizing: border-box; margin: 0; padding: 0; }
  html, body { width: 1200px; height: 716px; overflow: hidden; }
  body {
    background: var(--backdrop);
    font-family: "Roboto", Arial, sans-serif;
    position: relative;
  }
  .card {
    position: absolute;
    top: 210px;
    width: 520px;
    height: 297px;
    background: var(--card);
    border: 1px solid var(--card-edge);
    border-radius: 4px;
  }
  .card--front { left: 50px; }
  .card--back { left: 630px; }

  .wordmark { display: flex; align-items: flex-start; gap: 10px; }
  .wordmark__square { width: 14px; height: 14px; margin-top: 12px; }
  .wordmark__text { font-weight: 700; line-height: 1; }
  .wordmark__name { font-size: 48px; letter-spacing: 2px; }
  .wordmark__tagline { font-size: 14px; letter-spacing: 3.4px; margin-top: 6px; text-transform: uppercase; }

  .card--front .wordmark {
    position: absolute; left: 50%; top: 50%;
    transform: translate(-50%, -50%);
  }
  .card--front .wordmark__square { background: var(--gloss); }
  .card--front .wordmark__text { color: var(--gloss); }

  .card--back .wordmark { position: absolute; left: 34px; top: 64px; }
  .card--back .wordmark__name { font-size: 40px; }
  .card--back .wordmark__tagline { font-size: 12px; letter-spacing: 2.8px; }
  .card--back .wordmark__square { background: var(--red); margin-top: 10px; }
  .card--back .wordmark__text { color: var(--white); }

  .contact { position: absolute; left: 292px; top: 56px; color: var(--white); }
  .contact__name { color: var(--red); font-weight: 700; font-size: 19px; }
  .contact__title { font-size: 12px; color: var(--muted); margin-top: 2px; }
  .contact__list { list-style: none; margin-top: 14px; }
  .contact__item { display: flex; align-items: center; gap: 10px; font-size: 14px; line-height: 21px; }
  .contact__item svg { width: 11px; height: 11px; fill: var(--red); flex: none; }
  .social { display: flex; align-items: center; gap: 6px; margin-top: 12px; }
  .social__label { color: var(--red); font-size: 14px; }
  .social__icon { width: 16px; height: 16px; background: var(--white); border-radius: 2px; }
  .credentials { font-size: 15px; margin-top: 8px; letter-spacing: 0.3px; }
</style>
</head>
<body>
  <section class="card card--front" aria-label="Card front">
    <div class="wordmark">
      <span class="wordmark__square"></span>
      <div class="wordmark__text">
        <div class="wordmark__name">DULOM</div>
        <div class="wordmark__tagline">Home Remodeling</div>
      </div>
    </div>
  </section>

  <section class="card card--back" aria-label="Card back">
    <div class="wordmark">
      <span class="wordmark__square"></span>
      <div class="wordmark__text">
        <div class="wordmark__name">DULOM</div>
        <div class="wordmark__tagline">Home Remodeling</div>
      </div>
    </div>

    <div class="contact">
      <div class="contact__name">Karim Feltous</div>
      <div class="contact__title">CEO / General Contractor</div>
      <ul class="contact__list">
        <li class="contact__item">
          <svg viewBox="0 0 12 12"><path d="M2.5 0.5l2 2.2-1.1 1.4c.7 1.5 1.9 2.7 3.5 3.5l1.4-1.1 2.2 2-1.3 2.2C5 10.4 1.5 6.9 0.3 1.8z"/></svg>
          1-888-DULOM-47
        </li>
        <li class="contact__item">
          <svg viewBox="0 0 12 12"><path d="M2.5 0.5l2 2.2-1.1 1.4c.7 1.5 1.9 2.7 3.5 3.5l1.4-1.1 2.2 2-1.3 2.2C5 10.4 1.5 6.9 0.3 1.8z"/></svg>
          317-555-0193
        </li>
        <li class="contact__item">
          <svg viewBox="0 0 12 12"><path d="M0 2h12v8H0z M0.8 2.6L6 6.6l5.2-4" stroke="#131314" stroke-width="1"/></svg>
          info@dulomhome.com
        </li>
        <li class="contact__item">
          <svg viewBox="0 0 12 12"><circle cx="6" cy="6" r="5.5"/><path d="M0.5 6h11M6 0.5c-2.5 3-2.5 8 0 11M6 0.5c2.5 3 2.5 8 0 11" stroke="#131314" stroke-width="0.9" fill="none"/></svg>
          www.dulomhome.com
        </li>
      </ul>
      <div class="social">
        <span class="social__label">Follows on:</span>
        <span class="social__icon"></span>
        <span class="social__icon"></span>
        <span class="social__icon"></span>
      </div>
      <div class="credentials">Licensed &nbsp;•&nbsp; Insured &nbsp;•&nbsp; Bonded</div>
    </div>
  </section>
</body>
</html>
```